R.K. Bookkeeping Services Resumé

I am looking for a new design/look for a business resume. I have attached an example of another person's resume that gave me the inspiration to revamp our business resume. I am looking for something simple, fresh, not trendy, timeless, and at the same time innovative. I have attached the business card design, the resume, and the example of the resume that caught our eye. If you have any questions please feel free to ask.

Industry/Entity Type

Business

```html
<!DOCTYPE html>
<html lang="en">
<head>
<meta charset="utf-8">
<title>R.K. Bookkeeping Services – Resumé</title>
<link rel="stylesheet" href="https://fonts.googleapis.com/css2?family=Open+Sans:ital,wght@0,400;0,600;0,700;1,400;1,700&family=Roboto+Condensed:wght@400;700&display=swap">
<style>
  :root {
    --ink: #2e2e2e;
    --rule: #b5b5b5;
    --frame: #c9c9c9;
    --band: #e2e2e2;
    --dark: #3a3a3a;
    --faint: #cdcdcd;
    --paper: #ffffff;
  }
  * { box-sizing: border-box; margin: 0; padding: 0; }
  html, body { width: 849px; height: 1200px; overflow: hidden; background: var(--paper); }
  body { font-family: "Open Sans", Arial, sans-serif; color: var(--ink); font-size: 13px; line-height: 1.36; }

  .resume { position: relative; width: 849px; height: 1200px; }

  /* Header */
  .masthead { position: absolute; left: 0; top: 0; width: 849px; height: 106px; }
  .masthead__photo { position: absolute; inset: 0; background: linear-gradient(100deg, #dcdcdc 0%, #bdbdbd 45%, #8f8f8f 100%); }
  .brand { position: absolute; left: 24px; top: 20px; font-family: "Roboto Condensed", Arial, sans-serif; font-weight: 700; font-size: 34px; line-height: 1; color: var(--ink); display: flex; align-items: center; gap: 12px; }
  .brand__mark { width: 20px; height: 20px; background: var(--ink); }
  .tagline { position: absolute; left: 56px; top: 62px; font-family: "Roboto Condensed", Arial, sans-serif; font-size: 15px; letter-spacing: 1px; text-transform: uppercase; color: var(--ink); }

  .contact { position: absolute; right: 10px; top: 8px; width: 250px; list-style: none; display: flex; flex-direction: column; gap: 4px; }
  .contact li { display: flex; align-items: center; height: 20px; background: var(--paper); border: 1px solid var(--rule); }
  .contact__icon { width: 20px; height: 20px; background: var(--dark); display: flex; align-items: center; justify-content: center; flex: none; margin: -1px 0 -1px -1px; }
  .contact__text { padding-left: 7px; font-size: 12px; color: var(--ink); }
  .contact__text--name { font-weight: 700; }

  /* Frame and bands */
  .sheet { position: absolute; left: 8px; top: 106px; width: 833px; height: 1086px; border: 1px solid var(--frame); border-top: none; }
  .band { position: absolute; left: 9px; width: 831px; height: 12px; background: var(--band); }
  .band--mid { top: 368px; }
  .band--low { top: 978px; }
  .divider { position: absolute; left: 527px; top: 380px; width: 1px; height: 598px; background: var(--band); }

  .section-title { font-family: "Roboto Condensed", Arial, sans-serif; font-weight: 700; font-size: 19px; letter-spacing: .4px; text-transform: uppercase; color: var(--ink); padding-bottom: 4px; border-bottom: 2px solid var(--rule); margin-bottom: 9px; }

  .summary { position: absolute; left: 22px; top: 122px; width: 805px; }
  .summary p { margin-bottom: 8px; }
  .competencies { display: grid; grid-template-columns: repeat(4, 1fr); list-style: none; }
  .competencies li::before { content: "•"; margin-right: 7px; }

  .experience { position: absolute; left: 22px; top: 394px; width: 492px; }
  .job { margin-bottom: 11px; }
  .job__org { font-weight: 700; text-transform: uppercase; }
  .job__place { font-weight: 400; text-transform: none; font-style: italic; }
  .job__role { font-weight: 700; font-style: italic; }

  .software { position: absolute; left: 542px; top: 394px; width: 284px; }
  .software ul { list-style: none; }
  .software li { line-height: 1.42; }
  .software li::before { content: "•"; margin-right: 8px; }

  .brand-panel { position: absolute; left: 542px; top: 660px; width: 284px; height: 170px; border: 2px solid var(--band); display: flex; flex-direction: column; align-items: center; justify-content: center; gap: 10px; }
  .brand-panel__name { font-family: "Roboto Condensed", Arial, sans-serif; font-weight: 700; font-size: 30px; line-height: 1.1; color: var(--faint); text-align: center; }
  .brand-panel__mark { width: 16px; height: 16px; background: var(--faint); }

  .building { position: absolute; left: 600px; top: 850px; width: 170px; height: 110px; background: linear-gradient(180deg, #efefef, #d4d4d4); }

  .education { position: absolute; left: 22px; top: 1000px; width: 805px; }
  .degree { margin-bottom: 10px; }
  .degree__school { font-weight: 700; text-transform: uppercase; }
  .degree__place { font-weight: 400; text-transform: none; font-style: italic; }
  .degree__title { font-weight: 700; font-style: italic; }
</style>
</head>
<body>
<div class="resume">

  <header class="masthead">
    <div class="masthead__photo" role="img" aria-label="Greyscale photograph of a city street with buildings"></div>
    <div class="brand"><span class="brand__mark"></span>R.K.</div>
    <div class="tagline">Bookkeeping Services</div>
    <ul class="contact">
      <li>
        <span class="contact__icon"><svg width="11" height="11" viewBox="0 0 12 12"><circle cx="6" cy="3.5" r="2.5" fill="#fff"/><path d="M1 12c0-3 2.2-5 5-5s5 2 5 5z" fill="#fff"/></svg></span>
        <span class="contact__text contact__text--name">Dana Whitfield</span>
      </li>
      <li>
        <span class="contact__icon"><svg width="11" height="11" viewBox="0 0 12 12"><path d="M2.5 1l2 2.2-1 1.4c.8 1.6 2 2.8 3.6 3.6l1.4-1 2.2 2-1 1.8C5.5 11 1 6.5 1 2z" fill="#fff"/></svg></span>
        <span class="contact__text">618 555 0142</span>
      </li>
      <li>
        <span class="contact__icon"><svg width="11" height="11" viewBox="0 0 12 12"><rect x="1" y="2.5" width="10" height="7" fill="#fff"/><path d="M1 2.5l5 4 5-4" fill="none" stroke="#3a3a3a" stroke-width="1"/></svg></span>
        <span class="contact__text">rk@rkbkservices.com</span>
      </li>
      <li>
        <span class="contact__icon"><svg width="11" height="11" viewBox="0 0 12 12"><circle cx="6" cy="6" r="4.8" fill="none" stroke="#fff" stroke-width="1.2"/><path d="M1.2 6h9.6M6 1.2c-2.4 2.6-2.4 7 0 9.6M6 1.2c2.4 2.6 2.4 7 0 9.6" fill="none" stroke="#fff" stroke-width=".9"/></svg></span>
        <span class="contact__text">www.rkbkservices.com</span>
      </li>
    </ul>
  </header>

  <div class="sheet"></div>
  <div class="band band--mid"></div>
  <div class="divider"></div>
  <div class="band band--low"></div>

  <section class="summary">
    <h2 class="section-title">Accounting Manager + Controller</h2>
    <p><strong>Analytical Accounting Executive</strong> with demonstrated expertise in corporate finance management, reporting, forecasting, audits, tax preparation, and state and federal funding. Solid reputation as an expert problem solver who can resolve cross-functional business problems and develop productivity improvement initiatives resulting in increased profitability. Background includes proven success overseeing accounting and finance functions for healthcare organizations, higher education institutions, public and private schools, wholesalers, consulting firms, and logistics companies. Core competencies include:</p>
    <ul class="competencies">
      <li>Profit and Loss</li>
      <li>Business Analysis</li>
      <li>Risk Management</li>
      <li>Human Resources</li>
      <li>Financial Reporting</li>
      <li>Systems Automation</li>
      <li>Financial Analysis</li>
      <li>Modeling/Forecasting</li>
      <li>Audit/Compliance</li>
      <li>Efficiency Improvement</li>
      <li>Team Development</li>
      <li>Expense/Cost Control</li>
    </ul>
  </section>

  <section class="experience">
    <h2 class="section-title">Professional Experience</h2>

    <div class="job">
      <div class="job__org">R.K. Bookkeeping Services <span class="job__place">(2013 – Current)</span></div>
    </div>

    <div class="job">
      <div class="job__org">Carewell Management, LLC <span class="job__place">– Nashville, TN (04/11 – 05/13)</span></div>
      <div class="job__role">Accounting Manager / Controller</div>
      <p>Directed daily fiscal operations of $80 million home health agency, including accounting, financial planning and analysis, risk management, cost control, treasury, fixed assets and benefits administration. Managed staff of 35 employees.</p>
    </div>

    <div class="job">
      <div class="job__org">Harbor Parish Association <span class="job__place">– Nashville, TN (2007 – 2011)</span></div>
      <div class="job__role">Controller</div>
      <p>Directed all accounting functions for 24 parishes, including financial reporting, general ledger, A/P and A/R, budgeting, payroll, month-end and year-end closings and audit management. Supervised staff of 4 regional bookkeepers.</p>
    </div>

    <div class="job">
      <div class="job__org">Westbrook University <span class="job__place">– Nashville, TN (2006 – 2007)</span></div>
      <div class="job__role">Accountant</div>
    </div>

    <div class="job">
      <div class="job__org">Brookside City Schools <span class="job__place">– Brooklyn, OH (2005 – 2006)</span></div>
      <div class="job__role">Assistant Treasurer</div>
    </div>

    <div class="job">
      <div class="job__org">Lakeview &amp; Northern Ohio Data Consortium (LNODC) <span class="job__place">– Valley View, OH (2000 – 2001)</span></div>
      <div class="job__role">Fiscal Services Liaison</div>
    </div>

    <div class="job">
      <div class="job__org">Dorsey-Whitman Co. <span class="job__place">– Brooklyn, OH (1996 – 2000)</span></div>
      <div class="job__role">Accountant/Inventory Control</div>
    </div>

    <div class="job">
      <div class="job__org">Contract Ledger Services <span class="job__place">– Huntersville, NC (1991 – 1995)</span></div>
      <div class="job__role">Accounting Supervisor</div>
    </div>
  </section>

  <aside class="software">
    <h2 class="section-title">Software Programs</h2>
    <ul>
      <li>Paycrest</li>
      <li>PayBase</li>
      <li>Ledgerly</li>
      <li>BookTrack</li>
      <li>WageWise</li>
      <li>Ledger 90</li>
      <li>Oakline</li>
      <li>Swiftbook</li>
      <li>Parish Records Suite</li>
      <li>Office Works Suite</li>
      <li>FundPoint</li>
    </ul>
  </aside>

  <div class="brand-panel">
    <span class="brand-panel__mark"></span>
    <div class="brand-panel__name">R.K. Bookkeeping<br>Services</div>
  </div>
  <div class="building" role="img" aria-label="Faint grey illustration of a classical bank building"></div>

  <section class="education">
    <h2 class="section-title">Education</h2>
    <div class="degree">
      <div class="degree__school">Summit Ridge University <span class="degree__place">– Cleveland, OH</span></div>
      <div class="degree__title">Bachelor of Science – Business Management</div>
    </div>
    <div class="degree">
      <div class="degree__school">Lake Erie State University <span class="degree__place">– Cleveland, OH</span></div>
      <div class="degree__title">Completed School of Law and School of Finance Courses</div>
    </div>
  </section>

</div>
</body>
</html>
```